House-share and Room Rental Website (With Focus on the Bedroom Landing Page)

Looking for website design for our House-share (executive accommodation) and room rental business.

Our company name is: Lodgivo could also be written as LodGivo or lodgivo. Either is fine .. just looking for a nice clean catchy logo to go with the design.

EXAMPLES
These are examples of other websites in this field that are doing well. this is a kind of baseline.
https://nestpartners-example.com.au/
https://www.bunkora-example.com/
https://www.dwelzy-example.com/
https://www.habiquo-example.net/
https://www.cohabiscout-example.com.au/

Our business model is to rent rooms to people looking for high-quality accommodation. We fill the gap between those looking to rent rooms and those with rooms to rent. However, our model is slightly different from those already on the market as we looking to fill a massive gap in the market delivering upmarket rooms for rent.(Executive Accommodation) also in the back end will be coupled with a self management process in the back end.

We offer executive style accommodation that stands out above the rest. With special extras like fire safety.. and management processes that create happier homes. We are looking for a web design package that can help us grow and scale our business. We need a design that is captivating

Our MAIN focus is having a room landing page that stands out from the rest... The core of our business will rely on the promotion of the rooms in a share house... so the whole design relies on the BEDROOM landing page to drive results.

Target Market(s)

We have 2 markets we are aiming at ... the first market is people offering rooms to rent who want the highest rental return. The second market is people looking to rent safe, high-quality rooms, in houses that are well managed and looked after.

Industry/Entity Type

Share Economy

Logo Text

LodGivo

Number of Pages Required

5+ page

Font styles to use
Sans Serif

Colors
3276b5

Requirements
Must have
• A messaging system whereby we can create direct communication between those offering rooms and those looking for rooms.
• A call to action that says " Schedule an Inspection"
• Landing page for promoting rooms
• A home page for showing stock.
• Profile page for those selling rooms
• Profile page for those looking for rooms.
• A scheduling calendar for booking inspections
Nice to have
• Pages where new residents can lock in a room.. pay bond and rents.. and sign contracts
• Notifications
• SMS capabilities in the backend.
Should not have
• No script or handwriting fonts.

```html
<!DOCTYPE html>
<html lang="en">
<head>
<meta charset="utf-8">
<title>LodGivo – Room Details</title>
<link rel="stylesheet" href="https://fonts.googleapis.com/css2?family=Lato:wght@400;700;900&display=swap">
<style>
:root{
  --brand:#3276b5;
  --brand-deep:#1f4c93;
  --navy:#1b4a8c;
  --ink:#111;
  --text:#222;
  --muted:#555;
  --pale:#f1f5fb;
  --rule:#d8dde5;
  --map:#e2e3e5;
  --white:#fff;
}
*{box-sizing:border-box;margin:0;padding:0}
html,body{width:1200px;height:2568px;overflow:hidden;background:var(--white)}
body{position:relative;font-family:"Lato",sans-serif;color:var(--text)}

/* header */
.site-header{position:absolute;left:0;top:0;width:1200px;height:160px}
.site-header svg{position:absolute;left:0;top:0}
.brand-name{position:absolute;left:158px;top:38px;font-size:30px;font-weight:700;color:var(--white);letter-spacing:1px}
.main-nav{position:absolute;left:439px;top:49px;display:flex;gap:22px}
.main-nav a{color:var(--white);text-decoration:none;font-size:15.5px;font-weight:400}

/* room gallery + specs */
.photo{position:absolute;background:linear-gradient(135deg,#5a4a3e,#c9b9a5 55%,#3b302a)}
.photo.pool{background:linear-gradient(160deg,#2f8fb8,#8ec6d8 60%,#4a5d63)}
.photo.lounge{background:linear-gradient(160deg,#d9dce0,#a5927c 60%,#6d6253)}
.photo.deck{background:linear-gradient(160deg,#8a7f73,#3fb1cf 60%,#bfe4ef)}
.specs{position:absolute;left:674px;top:204px;font-size:19.5px;line-height:40px}
.specs .row{display:flex}
.specs dt{width:214px;color:var(--text)}
.specs dd{font-weight:700;color:var(--ink)}

/* info band */
.info-band{position:absolute;left:0;top:678px;width:1200px;height:274px;background:linear-gradient(180deg,#3f7fc0,#1f4c93);color:var(--white)}
.info-band .divider{position:absolute;top:0;width:1px;height:274px;background:rgba(255,255,255,.3)}
.info-col{position:absolute;top:58px}
.info-col h3{font-size:22px;font-weight:700;margin-bottom:14px}
.info-col p{font-size:17px;line-height:28px;opacity:.95}
.info-col .price{font-size:25px;margin-top:4px}

/* section headings */
.section-title{position:absolute;left:0;width:1200px;text-align:center;font-size:28px;font-weight:900;color:var(--ink);letter-spacing:.6px}
.section-title::after{content:"";display:block;width:64px;height:3px;background:var(--navy);margin:9px auto 0}

/* room amenities */
.room-amenities{position:absolute;left:0;top:952px;width:1200px;height:404px;background:var(--pale);border-bottom:2px solid var(--rule)}
.room-amenities .lead{position:absolute;top:108px;width:1200px;text-align:center;font-size:19px;color:var(--ink)}
.amenity{position:absolute;top:180px;width:140px;text-align:center}
.amenity .badge{width:72px;height:72px;border-radius:50%;background:var(--brand-deep);margin:0 auto;display:flex;align-items:center;justify-content:center}
.amenity .label{margin-top:18px;font-size:14.5px;font-weight:700;color:#333;line-height:18px;text-transform:uppercase}

/* public amenities */
.public-card{position:absolute;top:1478px;width:411px;height:132px;border:2px solid #e3e6ea;background:var(--white);display:flex;align-items:center;gap:16px;padding-left:24px;font-size:20px;font-weight:700;color:#333;line-height:30px}
.public-card.location{padding-left:57px}

/* map */
.map-area{position:absolute;left:0;top:1660px;width:1200px;height:527px}

/* footer */
.site-footer{position:absolute;left:0;top:2187px;width:1200px;height:381px}
.foot-col{position:absolute;top:56px}
.foot-col h4{font-size:19px;font-weight:700;color:var(--brand);margin-bottom:14px}
.foot-col ul{list-style:none}
.foot-col li{font-size:15px;color:#333;line-height:27px}
.contact-line{display:flex;gap:12px;font-size:15px;line-height:19px;color:#333;margin-bottom:15px}
.contact-line:first-of-type{margin-top:13px}
.social li{display:flex;align-items:center;gap:24px;padding-left:8px;line-height:34px}
.social .dot{width:10px;height:10px;border-radius:50%;background:#222}
.foot-rule{position:absolute;left:0;top:310px;width:1200px;height:1px;background:var(--rule)}
.copyright{position:absolute;top:332px;left:0;width:1212px;text-align:center;font-size:15px;color:#333}
</style>
</head>
<body>

<header class="site-header">
  <svg width="1200" height="160" viewBox="0 0 1200 160" aria-hidden="true">
    <polygon points="0,0 1200,0 1200,90 607,152 0,90" fill="#000"/>
    <polyline points="0,90 607,152 1200,90" fill="none" stroke="var(--navy)" stroke-width="6"/>
  </svg>
  <div class="brand-name">LODGIVO</div>
  <nav class="main-nav">
    <a href="#">ABOUT US</a><a href="#">OUR ROOMS</a><a href="#">TESTIMONIALS</a><a href="#">BLOGS</a><a href="#">BOOKING</a><a href="#">CONTACT</a>
  </nav>
</header>

<section class="room-overview">
  <div class="photo" style="left:146px;top:206px;width:469px;height:290px" role="img" aria-label="Photo of an executive bedroom with two beds and a desk"></div>
  <div class="photo pool" style="left:147px;top:504px;width:150px;height:106px" role="img" aria-label="Photo of the building pool"></div>
  <div class="photo lounge" style="left:308px;top:504px;width:150px;height:106px" role="img" aria-label="Photo of the outdoor lounge"></div>
  <div class="photo deck" style="left:471px;top:504px;width:149px;height:106px" role="img" aria-label="Photo of the pool deck"></div>

  <dl class="specs">
    <div class="row"><dt>Gender Preference :</dt><dd>MALE</dd></div>
    <div class="row"><dt>Size of room :</dt><dd>1200Sqm</dd></div>
    <div class="row"><dt>Bathroom :</dt><dd>Shared</dd></div>
    <div class="row"><dt>Parking :</dt><dd>Street</dd></div>
    <div class="row"><dt>Smoking :</dt><dd>Non-smoking</dd></div>
    <div class="row"><dt>Minimum contract :</dt><dd>(usually 3 months)</dd></div>
    <div class="row"><dt>Bed size :</dt><dd>6x4 Feet</dd></div>
    <div class="row"><dt>Type of housemates :</dt><dd>Students</dd></div>
    <div class="row"><dt>Room type :</dt><dd>shared</dd></div>
    <div class="row"><dt>Internet speed :</dt><dd>250 kbps</dd></div>
  </dl>
</section>

<section class="info-band">
  <span class="divider" style="left:390px"></span>
  <span class="divider" style="left:675px"></span>
  <div class="info-col" style="left:156px">
    <h3>Address</h3>
    <p>48 Linden Row #GA<br>Texas 75010 TX</p>
  </div>
  <div class="info-col" style="left:450px">
    <h3>Rental price</h3>
    <p class="price">$280 per day</p>
  </div>
  <div class="info-col" style="left:729px">
    <h3>Utilities - included/excluded</h3>
    <p>Mauris neque metus<br>Aalesuada nec<br>Altricies sit<br>Amet porttitor</p>
  </div>
</section>

<section class="room-amenities">
  <h2 class="section-title" style="top:50px">ROOM AMENITIES</h2>
  <p class="lead">these are some things that may be included in the room</p>

  <div class="amenity" style="left:130px">
    <div class="badge"><svg width="38" height="30" viewBox="0 0 38 30" fill="none" stroke="#fff" stroke-width="2.5"><rect x="2" y="4" width="34" height="5"/><path d="M7 9v18M31 9v18M7 18h24"/></svg></div>
    <div class="label">Furnished/<br>Unfurnished</div>
  </div>
  <div class="amenity" style="left:261px">
    <div class="badge"><svg width="36" height="32" viewBox="0 0 36 32" fill="none" stroke="#fff" stroke-width="2.5"><rect x="2" y="3" width="32" height="20"/><path d="M18 23v5M11 29h14"/></svg></div>
    <div class="label">TV</div>
  </div>
  <div class="amenity" style="left:379px">
    <div class="badge"><svg width="34" height="34" viewBox="0 0 34 34" fill="none" stroke="#fff" stroke-width="2.5"><path d="M5 14L9 4h16l4 10"/><rect x="3" y="14" width="28" height="16"/><path d="M3 21h28M14 25h6"/></svg></div>
    <div class="label">Storage<br>Space</div>
  </div>
  <div class="amenity" style="left:521px">
    <div class="badge"><svg width="38" height="36" viewBox="0 0 38 36" fill="none" stroke="#fff" stroke-width="2.5"><path d="M19 4v8M14 4h10"/><rect x="3" y="14" width="32" height="6"/><path d="M6 20v12M32 20v12M8 26h10"/></svg></div>
    <div class="label">Study Desk<br>/ Workstation</div>
  </div>
  <div class="amenity" style="left:651px">
    <div class="badge"><svg width="40" height="30" viewBox="0 0 40 30" fill="none" stroke="#fff" stroke-width="2.5"><path d="M16 7a4 4 0 1 1 4 4v4L3 25h34L20 15"/></svg></div>
    <div class="label">Wardrobe</div>
  </div>
  <div class="amenity" style="left:783px">
    <div class="badge"><svg width="36" height="36" viewBox="0 0 36 36" fill="#fff"><path d="M18 2v6" stroke="#fff" stroke-width="2.5"/><path d="M6 18a12 10 0 0 1 24 0z"/><circle cx="10" cy="23" r="1.6"/><circle cx="18" cy="23" r="1.6"/><circle cx="26" cy="23" r="1.6"/><circle cx="14" cy="28" r="1.6"/><circle cx="22" cy="28" r="1.6"/><circle cx="18" cy="33" r="1.6"/></svg></div>
    <div class="label">Ensuite<br>Shower</div>
  </div>
  <div class="amenity" style="left:912px">
    <div class="badge"><svg width="46" height="24" viewBox="0 0 46 24" fill="none" stroke="#fff" stroke-width="2.5"><rect x="2" y="4" width="42" height="16"/><path d="M14 4v16M30 4v16M8 10v4"/></svg></div>
    <div class="label">Kitchenette</div>
  </div>
</section>

<h2 class="section-title" style="top:1402px">PUBLIC AMENITIES</h2>
<div class="public-card" style="left:180px">
  <svg width="74" height="40" viewBox="0 0 74 40" fill="none" stroke="var(--navy)" stroke-width="3"><rect x="3" y="3" width="30" height="26" rx="4"/><path d="M3 16h30M9 29l-5 8M27 29l5 8"/><rect x="42" y="6" width="28" height="26" rx="5"/><path d="M42 18h28"/><circle cx="49" cy="35" r="2.5" fill="var(--navy)"/><circle cx="63" cy="35" r="2.5" fill="var(--navy)"/></svg>
  <span>TRANSPORT<br>OPTIONS: BUS</span>
</div>
<div class="public-card location" style="left:606px">
  <svg width="30" height="38" viewBox="0 0 30 38"><path d="M15 2C7 2 2 8 2 15c0 9 13 21 13 21s13-12 13-21c0-7-5-13-13-13z" fill="var(--navy)"/><circle cx="15" cy="15" r="5" fill="#fff"/></svg>
  <span>LOCATION OR DISTANCE<br>TO THE CITY- 120 KM</span>
</div>

<div class="map-area">
  <svg width="1200" height="527" viewBox="0 0 1200 527">
    <polygon points="0,96 588,6 1200,98 1200,527 0,527" fill="var(--map)" role="img" aria-label="Street map showing the room's location"/>
    <polyline points="0,96 588,6 1200,98" fill="none" stroke="var(--brand)" stroke-width="9"/>
    <path d="M623 218c-9 0-16 7-16 15 0 11 16 26 16 26s16-15 16-26c0-8-7-15-16-15z" fill="var(--brand)"/>
    <circle cx="623" cy="233" r="5" fill="#fff"/>
  </svg>
</div>

<footer class="site-footer">
  <div class="foot-col" style="left:165px">
    <h4>CONTACT US</h4>
    <div class="contact-line"><svg width="16" height="20" viewBox="0 0 16 20"><path d="M8 1C4 1 1 4 1 8c0 5 7 11 7 11s7-6 7-11c0-4-3-7-7-7z" fill="none" stroke="#222" stroke-width="1.6"/><circle cx="8" cy="8" r="2.3" fill="#222"/></svg><span>48 Linden Row #GA<br>Texas 75010 TX</span></div>
    <div class="contact-line"><svg width="16" height="16" viewBox="0 0 16 16"><path d="M3 1l3 3-2 2c1 2 3 4 6 6l2-2 3 3-2 2C7 15 1 9 1 3z" fill="none" stroke="#222" stroke-width="1.5"/></svg><span>555.014.2252</span></div>
    <div class="contact-line"><svg width="16" height="14" viewBox="0 0 16 14"><rect x="1" y="2" width="14" height="10" fill="none" stroke="#222" stroke-width="1.5"/><path d="M1 2l7 6 7-6" fill="none" stroke="#222" stroke-width="1.5"/></svg><span>info@lodgivo-example.com</span></div>
  </div>
  <div class="foot-col" style="left:445px">
    <h4>COMPANY</h4>
    <ul><li>Home</li><li>About us</li><li>Why Our Rooms</li><li>Testimonials</li><li>Contact</li></ul>
  </div>
  <div class="foot-col" style="left:635px">
    <h4>RESOURCES</h4>
    <ul><li>Managment</li><li>FAQ</li><li>Sitemap</li><li>Blogs</li><li>Gallery</li></ul>
  </div>
  <div class="foot-col" style="left:823px">
    <h4>GET IN TOUCH</h4>
    <ul class="social"><li><span class="dot"></span>Chirpline</li><li><span class="dot"></span>Friendlane</li><li><span class="dot"></span>Workmesh</li><li><span class="dot"></span>Snapgrid</li></ul>
  </div>
  <div class="foot-rule"></div>
  <p class="copyright">Copyright © 2019 All right reserved</p>
</footer>

</body>
</html>
```